Commercial Cleaning Company Website Design

We are working with Harbor Tidy Team. They are a commercial cleaning company that needs a new website design.

Some sites to use for inspiration:

https://www.plenvask.com
https://gleam-panecare.com
https://tidwellhelpers.net
https://quietnesthouse.com
https://www.thedustingbureau.com
https://www.pennytidy.com

Thank you for taking the time to consider designing a website for us. We are web developers based in Stockton and Los Angeles, CA, USA. Most of our projects go through the same process. Understanding this process may help you win a project with us. We custom-code all of our websites in-house. We don’t have any requirements as to what tools you use for your design, but we prefer Figma files. For any design that we label as four-stars, we send it to the client for review. The client picks the final design they want us to use. Once we complete this process, we will continue to show additional clients all the four-star sites and purchase them later. Your designs will have multiple chances to sell. For better chances of success, we ask that you follow these guidelines.

IMAGES:
If you use any images or icons in the design, we ask that you have a link to the asset so we can purchase the image/icon. Most of the designs we submit do not have the customer’s images on them unless they have some great images. Be creative; show us the feeling you are trying to portray with your image choices. Use any royalty-free site you choose. We subscribe to Adobe and mainly use their images, but we can purchase images outside of Adobe.

PLEASE NOTE: we will not submit designs to clients with watermarks on the images.

FONTS:
We ask that you identify the fonts used in the design. This can be done in a message if you want. We typically use Google Fonts and Adobe Fonts.

CONTENT:
We're always open to different content and ideas. We often submit designs with stock images so the client can see our vision. We typically take pictures after the website launch to use their images with our vision. Lorem Ipsum is fine for paragraphs, but we ask that you write the headers in correct English. We want to be able to show the vision and identify the sections of the website.

INSPIRATION:
We typically add a couple of links in the brief of websites we like to help you get started in your design.

REVISIONS:
We do not often ask for revisions of the designs unless we see something in the design that may not appeal to the client. If there are slight changes that we want to make, we do that in the development process.

FEEDBACK:
We rarely give feedback on designs during the design process. We are working on many website projects and do not have the time to provide feedback. We usually respond if your request is well thought out and asks specific questions, but a note asking “feedback, please” usually goes unanswered.

```html
<!DOCTYPE html>
<html lang="en">
<head>
<meta charset="utf-8">
<title>Harbor Tidy Team — Commercial Cleaning</title>
<link href="https://fonts.googleapis.com/css2?family=Poppins:wght@400;500;600;700&family=Montserrat:wght@400;500&display=swap" rel="stylesheet">
<style>
:root{
  --blue:#1f4fc4;
  --blue-dark:#1a45b5;
  --red:#f0302a;
  --orange:#f7941d;
  --yellow:#f9b214;
  --ink:#2b2b2b;
  --muted:#555;
  --light:#f2f4f9;
  --card:#f5f7fc;
  --white:#fff;
}
*{margin:0;padding:0;box-sizing:border-box}
html,body{width:1200px;height:4098px;overflow:hidden;background:var(--white)}
body{position:relative;font-family:'Poppins',sans-serif;color:var(--ink)}
.abs{position:absolute}
.btn{position:absolute;display:flex;align-items:center;justify-content:center;border-radius:30px;font-weight:600;font-size:15px;color:var(--white);background:linear-gradient(90deg,var(--red),var(--orange));text-transform:uppercase}
.btn-ghost{background:var(--white);color:var(--orange);box-shadow:0 4px 14px rgba(0,0,0,.12)}
.brand{position:absolute;display:flex;align-items:center;gap:14px}
.brand-mark{width:26px;height:26px;border-radius:50%;background:var(--red)}
.brand-name{font-family:'Poppins',sans-serif;font-weight:600;font-size:22px;letter-spacing:5px;color:var(--blue)}
/* header */
.header{position:absolute;left:0;top:0;width:1200px;height:138px;background:var(--white)}
.call-icon{left:622px;top:27px;width:46px;height:46px;border-radius:50%;background:var(--white);box-shadow:0 4px 14px rgba(0,0,0,.12);display:flex;align-items:center;justify-content:center}
.call-label{left:687px;top:27px;font-size:12px;color:#888}
.call-number{left:687px;top:44px;font-size:18px;font-weight:600;color:var(--blue)}
.call-divider{left:866px;top:32px;width:1px;height:40px;background:#ddd}
.nav{position:absolute;top:99px;left:439px;display:flex;gap:31px;font-size:15px;font-weight:600;color:#222}
.nav .active{color:var(--orange);border-bottom:2px solid var(--orange)}
/* hero */
.hero{position:absolute;left:0;top:138px;width:1200px;height:682px;overflow:hidden}
.hero-photo{position:absolute;inset:0;background:linear-gradient(120deg,#d9dde3 0%,#9aa3ad 45%,#59616b 75%,#c9a23a 100%)}
.hero-shade{position:absolute;inset:0;background:rgba(20,25,35,.35)}
.hero h1{position:absolute;left:0;top:205px;width:1200px;text-align:center;font-size:46px;line-height:56px;font-weight:600;color:var(--white)}
.hero p{position:absolute;left:0;top:318px;width:1200px;text-align:center;font-size:22px;line-height:31px;font-weight:500;color:var(--white)}
.dots{position:absolute;left:1137px;top:240px;display:flex;flex-direction:column;gap:12px}
.dots span{width:12px;height:12px;border-radius:50%;border:2px solid var(--white)}
.dots .on{background:var(--white)}
.hero-curve{position:absolute;left:0;bottom:0}
/* section titles */
.sec-dot{position:absolute;left:592px;width:16px;height:16px;border-radius:50%;background:var(--red)}
.sec-title{position:absolute;left:0;width:1200px;text-align:center;font-size:42px;font-weight:600;color:var(--blue)}
/* services */
.card{position:absolute;top:969px;width:317px;height:482px;background:var(--card);border-radius:16px;overflow:hidden;text-align:center}
.card.lift{background:var(--white);box-shadow:0 6px 24px rgba(0,0,0,.1)}
.card-photo{height:240px}
.card h3{margin-top:22px;font-size:20px;line-height:29px;font-weight:600;color:var(--blue)}
.card p{margin:16px 30px 0;font-family:'Montserrat',sans-serif;font-size:16px;line-height:24px;color:var(--ink)}
.card .btn{left:81px;top:409px;width:154px;height:46px}
.arrow{position:absolute;width:34px;height:34px;border-radius:50%;display:flex;align-items:center;justify-content:center}
.arrow.prev{background:#ccc}
.arrow.next{background:var(--blue)}
/* about */
.about{position:absolute;left:0;top:1572px;width:1200px;height:529px;background:var(--light)}
.about-photo{position:absolute;left:111px;top:72px;width:481px;height:385px;border-radius:16px;background:linear-gradient(135deg,#eef1f4,#b9c6d4 55%,#7fa8c9)}
.about h2{position:absolute;left:692px;top:98px;font-size:46px;font-weight:600;color:var(--blue)}
.about .about-dot{position:absolute;left:655px;top:115px;width:18px;height:18px;border-radius:50%;background:var(--red)}
.about h3{position:absolute;left:651px;top:172px;font-size:23px;font-weight:600;color:#111}
.about p{position:absolute;left:651px;top:214px;width:450px;font-family:'Montserrat',sans-serif;font-size:17px;line-height:27px;color:var(--ink)}
.about .btn{left:651px;top:398px;width:154px;height:46px}
/* why */
.why{position:absolute;left:0;top:2101px;width:1200px;height:566px;background:linear-gradient(90deg,#f2402e 0%,#f77a1f 55%,#f9a711 100%);color:var(--white)}
.why .sec-title{color:var(--white);top:125px}
.why .sec-dot{background:var(--white)}
.feature{position:absolute;width:240px;text-align:center}
.feature .icon{margin:0 auto;width:105px;height:105px;border-radius:50%;background:var(--blue);border:4px solid var(--white);display:flex;align-items:center;justify-content:center}
.feature h4{margin-top:24px;font-size:17px;line-height:25px;font-weight:600}
.feature p{margin-top:12px;font-family:'Montserrat',sans-serif;font-size:16px;line-height:24px}
/* reviews */
.review{position:absolute;top:2884px;width:306px;height:270px;background:var(--white);border-radius:16px;box-shadow:0 6px 24px rgba(0,0,0,.08);padding:24px 24px}
.stars{color:var(--orange);font-size:15px;letter-spacing:2px}
.review p{margin-top:8px;font-family:'Montserrat',sans-serif;font-size:13.5px;line-height:23px;color:#333}
.review hr{border:none;border-top:1px solid #ddd;margin-top:12px}
.reviewer{display:flex;align-items:center;gap:14px;margin-top:18px}
.avatar{width:56px;height:56px;border-radius:50%;background:linear-gradient(135deg,#c9cfd6,#7c8793)}
.reviewer b{display:block;font-size:15px;font-weight:600;color:var(--blue)}
.reviewer small{font-size:12px;color:#333}
/* contact */
.contact{position:absolute;left:0;top:3259px;width:1200px;height:473px;background:linear-gradient(180deg,#f3f4f7 0%,#fff 25%)}
.field{position:absolute;background:var(--white);box-shadow:0 3px 12px rgba(0,0,0,.1);font-size:13px;font-weight:500;color:#333;padding:12px 16px}
.contact .btn{left:516px;top:366px;width:168px;height:46px}
/* footer */
.footer{position:absolute;left:0;top:3732px;width:1200px;height:366px;background:var(--blue-dark);color:var(--white)}
.footer .brand-name{color:var(--white)}
.footer .brand-mark{background:var(--orange)}
.col-title{position:absolute;top:68px;font-size:17px;font-weight:600}
.links{position:absolute;top:106px;list-style:none;font-size:15px}
.links li{height:39px;display:flex;gap:22px}
.links li::before{content:"•";color:var(--yellow)}
.contact-row{position:absolute;left:800px;display:flex;align-items:center;gap:18px;font-size:15px;line-height:21px}
.contact-row .ico{width:36px;height:36px;border-radius:50%;background:var(--white);flex:none;display:flex;align-items:center;justify-content:center}
.footer-rule{position:absolute;left:111px;top:302px;width:978px;height:1px;background:rgba(255,255,255,.3)}
.copy{position:absolute;left:410px;top:322px;font-size:13px}
.social{position:absolute;top:313px;width:36px;height:36px;border-radius:50%;border:2px solid var(--white)}
.social.first{background:var(--red);border-color:var(--red)}
</style>
</head>
<body>

<header class="header">
  <div class="brand" style="left:111px;top:46px"><span class="brand-mark"></span><span class="brand-name">HARBOR TIDY TEAM</span></div>
  <div class="abs call-icon"><svg width="20" height="20" viewBox="0 0 24 24"><path fill="#f0302a" d="M6.6 10.8a15.1 15.1 0 0 0 6.6 6.6l2.2-2.2c.3-.3.7-.4 1-.2 1.1.4 2.3.6 3.6.6.6 0 1 .4 1 1V20c0 .6-.4 1-1 1A17 17 0 0 1 3 4c0-.6.4-1 1-1h3.5c.6 0 1 .4 1 1 0 1.3.2 2.5.6 3.6.1.3 0 .7-.2 1z"/></svg></div>
  <div class="abs call-label">CALL US:</div>
  <div class="abs call-number">+1 (555) 014 2290</div>
  <div class="abs call-divider"></div>
  <div class="btn" style="left:891px;top:25px;width:197px;height:47px">Request a Quote</div>
  <nav class="nav"><span class="active">HOME</span><span>ABOUT US</span><span>OUR SERVICES</span><span>REVIEWS</span><span>GALLERY</span><span>CONTACT US</span></nav>
</header>

<section class="hero">
  <div class="hero-photo" role="img" aria-label="Cleaner in yellow gloves wiping an office desk beside a laptop"></div>
  <div class="hero-shade"></div>
  <div class="sec-dot" style="top:130px;background:#fff"></div>
  <h1>YOUR CLEAN BUSINESS<br>STARTS HERE</h1>
  <p>Professional commercial cleaning services that keep your workspace<br>spotless, healthy, and ready for success.</p>
  <div class="btn" style="left:501px;top:403px;width:198px;height:46px">Request a Quote</div>
  <div class="dots"><span></span><span class="on"></span><span></span><span></span></div>
  <svg class="hero-curve" width="1200" height="682" viewBox="0 0 1200 682">
    <path fill="#1f4fc4" d="M0 682 L0 650 C160 560 380 535 620 555 C840 575 1010 560 1200 455 L1200 682 Z"/>
    <path fill="#fff" d="M0 682 C220 600 430 590 660 618 C860 642 1020 620 1200 540 L1200 682 Z"/>
  </svg>
</section>

<section>
  <div class="sec-dot" style="top:826px"></div>
  <h2 class="sec-title" style="top:880px">OUR SERVICES</h2>
  <div class="arrow prev" style="left:36px;top:1194px"><svg width="14" height="14" viewBox="0 0 14 14"><path d="M9 2 4 7l5 5" stroke="#fff" stroke-width="2.5" fill="none"/></svg></div>
  <div class="arrow next" style="left:1130px;top:1194px"><svg width="14" height="14" viewBox="0 0 14 14"><path d="M5 2l5 5-5 5" stroke="#fff" stroke-width="2.5" fill="none"/></svg></div>

  <article class="card" style="left:103px">
    <div class="card-photo" role="img" aria-label="Team vacuuming and wiping an open-plan office" style="background:linear-gradient(135deg,#e7ebef,#9fb3c6 60%,#4f7aa6)"></div>
    <h3>Office &amp; Workspace<br>Cleaning</h3>
    <p>Sed ut perspiciatis unde omnis iste natus error sit voluptatem accusantium.</p>
    <div class="btn btn-ghost">Learn More</div>
  </article>
  <article class="card lift" style="left:441px">
    <div class="card-photo" role="img" aria-label="Worker boots sweeping dust on a construction floor" style="background:linear-gradient(160deg,#c7c9cb,#8d8f92 60%,#5f5a55)"></div>
    <h3>Post-Construction<br>Cleaning</h3>
    <p>Sed ut perspiciatis unde omnis iste natus error sit voluptatem accusantium.</p>
    <div class="btn">Learn More</div>
  </article>
  <article class="card" style="left:780px">
    <div class="card-photo" role="img" aria-label="Rope-access worker cleaning skyscraper windows" style="background:linear-gradient(150deg,#9db5c9,#5f7f99 55%,#e58a2e)"></div>
    <h3>Window &amp; Glass<br>Cleaning</h3>
    <p>Sed ut perspiciatis unde omnis iste natus error sit voluptatem accusantium.</p>
    <div class="btn btn-ghost">Learn More</div>
  </article>
</section>

<section class="about">
  <div class="about-photo" role="img" aria-label="Cleaners vacuuming and mopping a bright modern office"></div>
  <span class="about-dot"></span>
  <h2>ABOUT US</h2>
  <h3>A Higher Standard of Clean.</h3>
  <p>At Harbor Tidy Team, we believe a clean environment reflects your company’s professionalism and care. From offices and retail spaces to industrial facilities, we deliver consistent, detail-driven cleaning services tailored to your schedule and standards.</p>
  <div class="btn">Learn More</div>
</section>

<section class="why" role="group" aria-label="Why choose us; background photo of cleaning staff tinted orange">
  <div class="sec-dot" style="top:80px"></div>
  <h2 class="sec-title">WHY CHOOSE US</h2>
  <div class="feature" style="left:103px;top:197px">
    <div class="icon"><svg width="50" height="40" viewBox="0 0 50 40" fill="#fff"><circle cx="25" cy="12" r="7"/><circle cx="10" cy="16" r="5"/><circle cx="40" cy="16" r="5"/><path d="M13 38c0-8 5-14 12-14s12 6 12 14z"/><path d="M1 38c0-6 4-11 9-11 2 0 3 .5 4 1-2 3-3 6-3 10zM49 38c0-6-4-11-9-11-2 0-3 .5-4 1 2 3 3 6 3 10z"/></svg></div>
    <h4>20+ YEARS OF<br>EXPERIENCE</h4>
    <p>Sed ut perspiciatis undeo iste natus error sit voluptatem accusantium doloremque.</p>
  </div>
  <div class="feature" style="left:354px;top:244px">
    <div class="icon"><svg width="50" height="50" viewBox="0 0 50 50"><circle cx="25" cy="25" r="20" fill="none" stroke="#fff" stroke-width="3"/><text x="25" y="31" text-anchor="middle" font-family="Poppins,sans-serif" font-weight="700" font-size="16" fill="#fff">24</text></svg></div>
    <h4>EMERGENCY SERVICES<br>AVAILABLE 24/7</h4>
    <p>Sed ut perspiciatis undeo iste natus error sit voluptatem accusantium doloremque.</p>
  </div>
  <div class="feature" style="left:606px;top:197px">
    <div class="icon"><svg width="48" height="48" viewBox="0 0 48 48"><circle cx="24" cy="24" r="18" fill="none" stroke="#fff" stroke-width="3"/><path d="M15 24l6 6 12-12" stroke="#fff" stroke-width="3.5" fill="none"/></svg></div>
    <h4>TRUSTED BY<br>INDUSTRY LEADERS</h4>
    <p>Sed ut perspiciatis undeo iste natus error sit voluptatem accusantium doloremque.</p>
  </div>
  <div class="feature" style="left:857px;top:244px">
    <div class="icon"><svg width="48" height="48" viewBox="0 0 48 48"><rect x="10" y="12" width="28" height="26" rx="3" fill="none" stroke="#fff" stroke-width="3"/><path d="M16 22h16M16 28h16M16 34h10" stroke="#fff" stroke-width="3"/></svg></div>
    <h4>END-TO-END<br>PROJECT MANAGEMENT</h4>
    <p>Sed ut perspiciatis undeo iste natus error sit voluptatem accusantium doloremque.</p>
  </div>
</section>

<section>
  <div class="sec-dot" style="top:2740px"></div>
  <h2 class="sec-title" style="top:2800px">WHAT OUR CLIENTS SAY</h2>
  <div class="arrow prev" style="left:36px;top:3002px"><svg width="14" height="14" viewBox="0 0 14 14"><path d="M9 2 4 7l5 5" stroke="#fff" stroke-width="2.5" fill="none"/></svg></div>
  <div class="arrow next" style="left:1130px;top:3002px"><svg width="14" height="14" viewBox="0 0 14 14"><path d="M5 2l5 5-5 5" stroke="#fff" stroke-width="2.5" fill="none"/></svg></div>
  <article class="review" style="left:111px">
    <div class="stars">★★★★★</div>
    <p>Lorem ipsum dolor sit amet, consecte adipiscing elit, sed do eiusmod temp incididunt ut labore et dolore magna aliqua. Ut enim ad minim veniam, qui nostrud exercitationea.</p>
    <hr>
    <div class="reviewer"><div class="avatar" role="img" aria-label="Client portrait"></div><div><b>MARCUS HALE</b><small>United States</small></div></div>
  </article>
  <article class="review" style="left:447px">
    <div class="stars">★★★★★</div>
    <p>Lorem ipsum dolor sit amet, consecte adipiscing elit, sed do eiusmod temp incididunt ut labore et dolore magna aliqua. Ut enim ad minim veniam, qui nostrud exercitationea.</p>
    <hr>
    <div class="reviewer"><div class="avatar" role="img" aria-label="Client portrait"></div><div><b>MARCUS HALE</b><small>United States</small></div></div>
  </article>
  <article class="review" style="left:783px">
    <div class="stars">★★★★★</div>
    <p>Lorem ipsum dolor sit amet, consecte adipiscing elit, sed do eiusmod temp incididunt ut labore et dolore magna aliqua. Ut enim ad minim veniam, qui nostrud exercitationea.</p>
    <hr>
    <div class="reviewer"><div class="avatar" role="img" aria-label="Client portrait"></div><div><b>MARCUS HALE</b><small>United States</small></div></div>
  </article>
</section>

<section class="contact">
  <div class="sec-dot" style="top:70px"></div>
  <h2 class="sec-title" style="top:123px">GET IN TOUCH</h2>
  <div class="field" style="left:202px;top:203px;width:392px;height:39px">Full Name</div>
  <div class="field" style="left:202px;top:255px;width:392px;height:38px">Phone</div>
  <div class="field" style="left:202px;top:306px;width:392px;height:40px">Email</div>
  <div class="field" style="left:605px;top:203px;width:393px;height:143px">Type Your Message</div>
  <div class="btn">Send Message</div>
</section>

<footer class="footer">
  <div class="brand" style="left:111px;top:152px"><span class="brand-mark"></span><span class="brand-name">HARBOR TIDY TEAM</span></div>
  <div class="col-title" style="left:430px">NAVIGATION</div>
  <ul class="links" style="left:430px"><li>Home</li><li>About Us</li><li>Our Services</li><li>Reviews</li><li>Gallery</li></ul>
  <div class="col-title" style="left:600px">QUICK LINKS</div>
  <ul class="links" style="left:600px"><li>Contact Us</li><li>Privacy Policy</li><li>Terms Of Use</li><li>Disclaimer</li></ul>
  <div class="col-title" style="left:800px">CONTACT US</div>
  <div class="contact-row" style="top:104px"><span class="ico"><svg width="14" height="18" viewBox="0 0 14 18"><path fill="#f7941d" d="M7 0a7 7 0 0 0-7 7c0 5 7 11 7 11s7-6 7-11a7 7 0 0 0-7-7zm0 9.5A2.5 2.5 0 1 1 7 4.5a2.5 2.5 0 0 1 0 5z"/></svg></span><span>212 Quayside Lane, Stockton,<br>CA</span></div>
  <div class="contact-row" style="top:164px"><span class="ico"><svg width="18" height="14" viewBox="0 0 18 14"><rect width="18" height="14" rx="2" fill="#f7941d"/><path d="M1 2l8 6 8-6" stroke="#fff" stroke-width="1.5" fill="none"/></svg></span><span>info@harbortidyteam.com</span></div>
  <div class="contact-row" style="top:218px"><span class="ico"><svg width="16" height="16" viewBox="0 0 24 24"><path fill="#f7941d" d="M6.6 10.8a15.1 15.1 0 0 0 6.6 6.6l2.2-2.2c.3-.3.7-.4 1-.2 1.1.4 2.3.6 3.6.6.6 0 1 .4 1 1V20c0 .6-.4 1-1 1A17 17 0 0 1 3 4c0-.6.4-1 1-1h3.5c.6 0 1 .4 1 1 0 1.3.2 2.5.6 3.6.1.3 0 .7-.2 1z"/></svg></span><span>+1 (555) 014 2290</span></div>
  <div class="footer-rule"></div>
  <div class="copy">© 2025 HARBOR TIDY TEAM &nbsp;|&nbsp; All Rights Reserved</div>
  <span class="social first" style="left:966px" aria-label="Social profile"></span>
  <span class="social" style="left:1009px" aria-label="Social profile"></span>
  <span class="social" style="left:1052px" aria-label="Social profile"></span>
</footer>

</body>
</html>
```